Financial Services Consultant needs a business card

We need a business card for a new consulting company based in Melbourne called
"Quelbrook Insights". Tagline is Measure, Monitor, Save
We would like to see business card designs that are in line with the minimal style of the website www.quelbrook-insights.example
The font I have used on the website is Proxima Nova and would like the same or similar font used on the business card with a minimal design in line with the website Two sided with "QUELBROOK INSIGHTS" MEASURE, MONITOR, SAVE on one side and name, title and contact details on the otther
Updates

Hi All, thanks for your submissions, much appreciated.

I have recently added some colour to my webiste, it is hex #3a7b74 for those that wish to use it
Thanks

Hi all

thanks very much for your design submissions I am very impressed and they are much appreciated.

Interms of general feedback please find below;

Colour: I am trying to stick to a minimal design and colour scheme for my website which is still under construction, up to 3 colours( www.quelbrook-insights.example) it is currently black and white with a small amount of blue/green but I am open to suggestion/interpretations for a consulting company.

Card: I dont mind if it has rounded edges or straight, I was thinking about using a letterpress card if possible

Detail: the detail on the card will include; Name, Title, Mobile, Personal Email, Business Email,Web,Business Address

Once again thanks for submissions

Industry/Entity Type

Business

```html
<!DOCTYPE html>
<html lang="en">
<head>
<meta charset="utf-8">
<title>Quelbrook Insights — Business Card Front</title>
<link href="https://fonts.googleapis.com/css2?family=Montserrat:wght@400;700&display=swap" rel="stylesheet">
<style>
  :root {
    --page-bg: #ffffff;
    --card-bg: #ffffff;
    --card-edge: #8a8a8a;
    --card-shadow: #c6c6c6;
    --brand-green: #33936b;
    --ink: #111111;
  }
  html, body {
    margin: 0;
    padding: 0;
    width: 1200px;
    height: 1000px;
    overflow: hidden;
    background: var(--page-bg);
  }
  .card-canvas {
    display: block;
    width: 1200px;
    height: 1000px;
  }
  .card-shadow { fill: var(--card-shadow); }
  .card-face { fill: var(--card-bg); stroke: var(--card-edge); stroke-width: 1; }
  .grid-rule { stroke: var(--brand-green); stroke-width: 2; fill: none; }
  .brand-name {
    font-family: "Montserrat", "Proxima Nova", sans-serif;
    font-weight: 700;
    font-size: 70px;
    fill: var(--brand-green);
  }
  .tagline-bullet { fill: var(--brand-green); }
  .tagline-word {
    font-family: "Montserrat", "Proxima Nova", sans-serif;
    font-weight: 400;
    font-size: 50px;
    fill: var(--ink);
  }
</style>
</head>
<body>
<svg class="card-canvas" viewBox="0 0 1200 1000" xmlns="http://www.w3.org/2000/svg" role="img" aria-label="Quelbrook Insights business card: Measure, Monitor, Save">
  <!-- Card body -->
  <rect class="card-shadow" x="86" y="213" width="1050" height="610"/>
  <rect class="card-face" x="76.5" y="201.5" width="1049" height="599"/>

  <!-- Column and row rules -->
  <line class="grid-rule" x1="337" y1="202" x2="337" y2="800"/>
  <line class="grid-rule" x1="941" y1="202" x2="941" y2="800"/>
  <line class="grid-rule" x1="337" y1="531" x2="941" y2="531"/>
  <line class="grid-rule" x1="337" y1="655" x2="941" y2="655"/>

  <!-- Vertical brand name -->
  <g class="brand-block">
    <text class="brand-name" transform="translate(205 752) rotate(-90)" x="0" y="0" textLength="520" lengthAdjust="spacingAndGlyphs">QUELBROOK</text>
    <text class="brand-name" transform="translate(295 752) rotate(-90)" x="0" y="0" textLength="480" lengthAdjust="spacingAndGlyphs">INSIGHTS</text>
  </g>

  <!-- Tagline list -->
  <g class="tagline-list">
    <circle class="tagline-bullet" cx="406" cy="492" r="13"/>
    <text class="tagline-word" x="480" y="510" textLength="382" lengthAdjust="spacing">MEASURE</text>

    <circle class="tagline-bullet" cx="406" cy="599" r="13"/>
    <text class="tagline-word" x="480" y="617" textLength="382" lengthAdjust="spacing">MONITOR</text>

    <circle class="tagline-bullet" cx="406" cy="707" r="13"/>
    <text class="tagline-word" x="480" y="725" textLength="210" lengthAdjust="spacing">SAVE</text>
  </g>
</svg>
</body>
</html>
```